A5 Flyer for Financial Services Business

I am after a re-design of our business flyer to fit in with our new branding style and logo colour scheme. Wanting something with a bit of designer flair that I could not create myself. I have included the flyer which I created which lacks style so dazzle me.

I want to use the same content.

Text for main body of flyer is

Are you a small business owner, tradie or TRPQ Service Provider struggling to stay on top of your bookkeeping and compliance obligations? If so we would love to help you get back on track and take control of your business finances so that you can make informed business decisions and focus on what you do best.

We have over 20 years industry experience and, as a small business ourselves, we are able to offer our clients a personal bookkeeping solution tailored to meet the needs of your business.

Accounts Payable | Accounts Receivable
Customer Invoicing
Bank and Credit Card Reconciliations
Payroll | Superannuation | Payroll Tax
Business Activity | Instalment Activity Statements
Regular Financial Reports
Vantly and Brimfolk Set-Up and Training

```html
<!DOCTYPE html>
<html lang="en">
<head>
<meta charset="utf-8">
<title>Even Keel Financial Services – Bookkeeping Flyer</title>
<link rel="stylesheet" href="https://fonts.googleapis.com/css2?family=Montserrat:wght@400;500;600;700;800&family=Roboto:wght@300;400;700&display=swap">
<style>
  :root {
    --navy: #0f4c6c;
    --teal: #0d7f8d;
    --teal-deep: #0b6f7c;
    --bright-blue: #1b9ee0;
    --heading-blue: #17527e;
    --badge-blue: #1d3a94;
    --wash: #e4f4f9;
    --paper: #f7fbfc;
    --grey: #cfd2d4;
    --grey-light: #e2e4e5;
    --ink: #1f2326;
    --white: #ffffff;
  }
  * { box-sizing: border-box; margin: 0; padding: 0; }
  html, body { width: 901px; height: 1200px; overflow: hidden; background: var(--white); }
  .flyer {
    position: relative; width: 901px; height: 1200px; overflow: hidden;
    background: var(--paper);
    font-family: "Montserrat", Arial, sans-serif; color: var(--ink);
  }
  .shapes { position: absolute; inset: 0; }
  .abs { position: absolute; }

  .agent-badge { left: 64px; top: 31px; width: 80px; height: 80px; border-radius: 50%; background: #9cc83a; border: 6px solid var(--white); }
  .agent-label { left: 164px; top: 56px; color: var(--white); font-size: 16px; line-height: 21px; font-weight: 400; }

  .brand { right: 52px; top: 116px; text-align: right; color: #1a7f8e; font-family: "Roboto", Arial, sans-serif; font-weight: 300; }
  .brand-name { font-size: 40px; letter-spacing: 0.5px; line-height: 44px; }
  .brand-sub { font-size: 19px; letter-spacing: 8.5px; line-height: 24px; margin-right: -8px; }

  .headline { right: 51px; top: 236px; text-align: right; color: var(--white); font-family: "Roboto", Arial, sans-serif; font-size: 40px; line-height: 49px; font-weight: 400; }
  .headline strong { font-weight: 700; }

  .intro { left: 0; top: 573px; width: 901px; height: 142px; background: var(--wash); padding: 22px 40px 0 45px; font-size: 17.6px; line-height: 26px; font-weight: 500; }
  .intro em, .experience em { font-style: normal; font-weight: 700; color: var(--heading-blue); }

  .years { left: 66px; top: 742px; width: 250px; display: flex; align-items: baseline; gap: 8px; color: var(--badge-blue); }
  .years-number { font-size: 78px; line-height: 84px; font-weight: 800; letter-spacing: -3px; }
  .years-word { font-size: 30px; line-height: 34px; font-weight: 700; }

  .experience { left: 341px; top: 748px; width: 530px; font-size: 17.4px; line-height: 26px; font-weight: 500; }
  .experience em { font-size: 19px; }

  .services { left: 0; top: 0; width: 901px; height: 1200px; list-style: none; }
  .service { position: absolute; display: flex; align-items: flex-start; gap: 22px; font-size: 17.4px; line-height: 22px; font-weight: 500; }
  .service svg { flex: none; width: 36px; height: 38px; margin-top: -2px; }

  .phone { left: 62px; top: 1133px; color: var(--white); font-weight: 600; font-size: 22px; display: flex; align-items: center; gap: 10px; }
  .contacts { left: 430px; top: 1117px; font-size: 16.4px; line-height: 28px; font-weight: 500; color: var(--ink); }
  .contacts li { list-style: none; display: flex; align-items: center; gap: 12px; }
  .contacts svg { width: 16px; height: 16px; }
</style>
</head>
<body>
<main class="flyer">
  <svg class="shapes" width="901" height="1200" viewBox="0 0 901 1200" aria-hidden="true">
    <polygon points="0,0 258,0 356,132 0,132" fill="var(--navy)"/>
    <polygon points="683,567 901,515 901,567" fill="var(--grey-light)"/>
    <polygon points="356,1103 901,1103 901,1186 330,1186" fill="var(--grey)"/>
    <polygon points="0,1104 302,1104 256,1200 0,1200" fill="var(--teal)"/>
    <polygon points="0,1100 305,1100 300,1112 0,1112" fill="var(--navy)"/>
    <polygon points="372,1074 412,1074 330,1200 288,1200" fill="var(--bright-blue)"/>
    <polygon points="412,1074 452,1074 372,1200 330,1200" fill="var(--teal-deep)"/>
  </svg>
  <div class="abs" role="img" aria-label="Photo of hands working with a calculator, laptop, folders and paperwork on a desk"
       style="left:0;top:142px;width:683px;height:425px;clip-path:polygon(0 0,450px 0,683px 425px,0 425px);background:linear-gradient(135deg,#dfe6ea 0%,#c6d1d6 45%,#eef1f2 100%);"></div>
  <svg class="shapes" width="901" height="1200" viewBox="0 0 901 1200" aria-hidden="true">
    <polygon points="410,204 901,204 901,515 576,515" fill="var(--teal)"/>
  </svg>

  <div class="abs agent-badge" role="img" aria-label="Registered agent badge"></div>
  <p class="abs agent-label">BAS Agent<br>10482730</p>

  <div class="abs brand">
    <p class="brand-name">EVEN KEEL</p>
    <p class="brand-sub">Financial Services</p>
  </div>

  <h1 class="abs headline"><strong>Affordable</strong><br><strong>Bookkeeping</strong><br><strong>Tailored</strong> to your<br>Business<br>needs</h1>

  <p class="abs intro"><em>Are you a small business owner, tradie or TRPQ Service</em> Provider struggling to<br>stay on top of your bookkeeping and compliance obligations? If so we would<br>love to help you get back on track and take control of your business finances so<br>that you can make informed business decisions and focus on what you do best.</p>

  <p class="abs years"><span class="years-number">20</span><span class="years-word">years</span></p>
  <p class="abs experience"><em>Industry experience</em> and, as a small business<br>ourselves, we are able to offer our clients a<br>personal bookkeeping solution tailored to meet the<br>needs of your business.</p>

  <svg width="0" height="0" style="position:absolute">
    <defs>
      <linearGradient id="hexFill" x1="0" y1="0" x2="0" y2="1">
        <stop offset="0" stop-color="#2bb3e6"/><stop offset="1" stop-color="#0d7f8d"/>
      </linearGradient>
      <symbol id="hex" viewBox="0 0 36 38">
        <polygon points="18,1 34,10 34,28 18,37 2,28 2,10" fill="url(#hexFill)"/>
        <polygon points="18,6 30,13 30,25 18,32 6,25 6,13" fill="var(--white)"/>
        <polygon points="18,8 28,14 28,24 18,30 8,24 8,14" fill="#33aee0"/>
      </symbol>
    </defs>
  </svg>
  <ul class="abs services">
    <li class="service" style="left:72px;top:888px"><svg><use href="#hex"/><text x="18" y="24" text-anchor="middle" font-size="15" font-weight="700" fill="#fff" font-family="Montserrat, sans-serif">1</text></svg><span>Business Activity |<br>Instalment Activity Statements</span></li>
    <li class="service" style="left:501px;top:888px"><svg><use href="#hex"/><text x="18" y="24" text-anchor="middle" font-size="15" font-weight="700" fill="#fff" font-family="Montserrat, sans-serif">2</text></svg><span>Vantly and Brimfolk Set-Up<br>and Training</span></li>
    <li class="service" style="left:72px;top:955px"><svg><use href="#hex"/><text x="18" y="24" text-anchor="middle" font-size="15" font-weight="700" fill="#fff" font-family="Montserrat, sans-serif">3</text></svg><span>Bank and Credit Card<br>Reconciliations</span></li>
    <li class="service" style="left:501px;top:955px"><svg><use href="#hex"/><text x="18" y="24" text-anchor="middle" font-size="15" font-weight="700" fill="#fff" font-family="Montserrat, sans-serif">4</text></svg><span>Payroll | Superannuation |<br>Payroll Tax</span></li>
    <li class="service" style="left:72px;top:1022px"><svg><use href="#hex"/><text x="18" y="24" text-anchor="middle" font-size="15" font-weight="700" fill="#fff" font-family="Montserrat, sans-serif">5</text></svg><span>Accounts Payable |<br>Accounts Receivable</span></li>
    <li class="service" style="left:501px;top:1022px"><svg><use href="#hex"/><text x="18" y="24" text-anchor="middle" font-size="15" font-weight="700" fill="#fff" font-family="Montserrat, sans-serif">6</text></svg><span>Regular Financial Reports I<br><span style="display:inline-block;margin-top:8px">Customer Invoicing</span></span></li>
  </ul>

  <p class="abs phone">
    <svg width="20" height="20" viewBox="0 0 24 24" aria-hidden="true"><path fill="#fff" d="M6.6 10.8a15.1 15.1 0 0 0 6.6 6.6l2.2-2.2c.3-.3.7-.4 1-.2 1.1.4 2.300.6 3.600.6.6 0 1 .4 1 1V20c0 .6-.4 1-1 1A17 17 0 0 1 3 4c0-.6.4-1 1-1h3.5c.6 0 1 .4 1 1 0 1.3.2 2.5.6 3.6.1.3 0 .7-.2 1z"/></svg>
    1300 555 014
  </p>
  <ul class="abs contacts">
    <li><svg viewBox="0 0 24 24" aria-hidden="true"><circle cx="12" cy="12" r="9" fill="none" stroke="#0f4c6c" stroke-width="2"/><path d="M3 12h18M12 3c3 3 3 15 0 18M12 3c-3 3-3 15 0 18" fill="none" stroke="#0f4c6c" stroke-width="1.6"/></svg>evenkeelfinancialservices.com</li>
    <li><svg viewBox="0 0 24 24" aria-hidden="true"><rect x="2" y="5" width="20" height="14" fill="#0f4c6c"/><path d="M2 5l10 8 10-8" fill="none" stroke="#fff" stroke-width="1.6"/></svg>info@evenkeelfinancialservices.com.au</li>
  </ul>
</main>
</body>
</html>
```